Thornbury Building Company - Card Design

I am looking to use the logo designs that you already did for me to develop a business card. I would like the card to have a black background and be double sided. I want white and green logo and text. I have attached an inspiration photo of a look that I like. I would like to use the Vertical Logo attached to take up the full front side of the card. On the back where I have my name and information, I would like to have the horizontal logo or maybe even just the image of the 'A' and trees without the text. I am open, but I am looking for something clean and simple and I want the green to really pop! Additional files can be found under Design #: 58302946

Target Market(s)

Homeowners

Industry/Entity Type

Construction

Contact Information for Business Card

Name: Marcus Thornbury, Title: Project Manager, Phone: 555.274.8136, Email: thornburybuildingcompany@mailvesta.com, address: 487 Larkspur Ln, Brookvale, CA 95033, Lic# 2468317

Colors
00AB8E
00BBA5
67D7C9
C6EFE9
E9F9F6

Requirements
Nice to have
• I would like to see the logos that I have already got from ArtLoomHub, though I am open to new ones

```html
<!DOCTYPE html>
<html lang="en">
<head>
<meta charset="utf-8">
<title>Thornbury Building Company – Business Card</title>
<link href="https://fonts.googleapis.com/css2?family=Open+Sans:wght@400;600;700&display=swap" rel="stylesheet">
<style>
  :root {
    --backdrop: #4b4b4b;
    --card-black: #161616;
    --green: #6db544;
    --green-bright: #3dba4e;
    --white: #ffffff;
  }
  * { box-sizing: border-box; margin: 0; padding: 0; }
  html, body {
    width: 1200px; height: 801px; overflow: hidden;
    background: var(--backdrop);
    font-family: "Open Sans", Arial, sans-serif;
  }
  .canvas {
    position: relative; width: 1200px; height: 801px;
    display: flex; align-items: center; justify-content: center; gap: 40px;
  }
  .card {
    position: relative; width: 540px; height: 309px;
    background: var(--card-black); overflow: hidden;
    box-shadow: 0 12px 30px rgba(0,0,0,.35);
  }

  /* Contact side */
  .card-front { border-bottom: 2px solid var(--green); }
  .brand-block {
    position: absolute; top: 34px; left: 220px; width: 300px; text-align: center;
  }
  .brand-estd {
    display: flex; justify-content: space-between;
    font-size: 9px; letter-spacing: 3px; color: var(--white);
    padding: 0 8px; margin-bottom: 8px;
  }
  .brand-name {
    font-weight: 700; color: var(--white);
    font-size: 22px; line-height: 1.15; letter-spacing: .5px;
  }
  .person { position: absolute; left: 26px; top: 168px; }
  .person-name { color: var(--green); font-weight: 700; font-size: 22px; line-height: 1.1; }
  .person-title { color: var(--white); font-size: 14px; margin-top: 2px; }
  .divider {
    position: absolute; left: 26px; right: 26px; top: 226px;
    height: 1px; background: var(--green);
  }
  .contact-left, .contact-right {
    position: absolute; top: 236px; color: var(--white); font-size: 12px; line-height: 1.65;
  }
  .contact-left { left: 26px; }
  .contact-right { right: 26px; text-align: right; }
  .contact-row { display: flex; align-items: center; gap: 6px; white-space: nowrap; }
  .contact-row svg { width: 11px; height: 11px; flex: none; }
  .footer-rule {
    position: absolute; left: 0; right: 0; bottom: 20px; height: 2px; background: var(--white);
  }
  .footer-band {
    position: absolute; left: 0; right: 0; bottom: 0; height: 17px; background: var(--green);
  }

  /* Brand side */
  .card-back {
    border-bottom: 2px solid var(--green); border-left: 2px solid var(--green);
    display: flex; flex-direction: column; align-items: center; justify-content: center;
  }
  .back-brand { display: flex; align-items: center; gap: 14px; }
  .back-dot { width: 26px; height: 26px; border-radius: 50%; background: var(--green-bright); flex: none; }
  .back-name {
    color: var(--white); font-weight: 700; font-size: 28px; line-height: 1.1; letter-spacing: .5px;
  }
  .back-estd {
    margin-top: 16px; color: var(--white); font-size: 10px; letter-spacing: 4px; text-align: center;
    border-top: 1px solid var(--green); padding-top: 4px;
  }
</style>
</head>
<body>
<main class="canvas">

  <section class="card card-front" aria-label="Business card, contact side">
    <div class="brand-block">
      <div class="brand-estd"><span>ESTD</span><span>2017</span></div>
      <div class="brand-name">Thornbury<br>Building Company</div>
    </div>

    <div class="person">
      <div class="person-name">Marcus Thornbury</div>
      <div class="person-title">Project Manager</div>
    </div>

    <div class="divider"></div>

    <div class="contact-left">
      <div class="contact-row">
        <svg viewBox="0 0 12 12" aria-hidden="true"><path d="M2.5 1h2l1 3-1.3.9a6 6 0 0 0 2.9 2.9L8 6.5l3 1v2A1.5 1.5 0 0 1 9.5 11 8.5 8.5 0 0 1 1 2.5 1.5 1.5 0 0 1 2.5 1z" fill="var(--green)"/></svg>
        <span>555.274.8136</span>
      </div>
      <div class="contact-row">
        <svg viewBox="0 0 12 12" aria-hidden="true"><rect x="1" y="2.5" width="10" height="7" fill="var(--green)"/><path d="M1 2.5l5 4 5-4" stroke="var(--card-black)" stroke-width="1" fill="none"/></svg>
        <span>thornburybuildingcompany@mailvesta.com</span>
      </div>
    </div>

    <div class="contact-right">
      <div>487 Larkspur Ln, Brookvale, CA 95033</div>
      <div>Lic # 2468317</div>
    </div>

    <div class="footer-rule"></div>
    <div class="footer-band"></div>
  </section>

  <section class="card card-back" aria-label="Business card, brand side">
    <div class="back-brand">
      <span class="back-dot"></span>
      <span class="back-name">Thornbury<br>Building Company</span>
    </div>
    <div class="back-estd">ESTD 2017</div>
  </section>

</main>
</body>
</html>
```